Whirlwind Mabel Launching in New Location

I need a marketing postcard that announces the opening of Whirlwind Mabel! It should grab the attention of the target market by highlighting the services they could use the most. I want them to look at this postcard and say, "Oh my god, I totally need this!" Whirlwind Mabel is all about putting time back in the lives of busy working people by taking every day tasks off their "to do" lists.

If using pictures, I'd like a more retro look and feel. Whirlwind Mabel reminds me of the 50' and 60's. Parents and families juggling multiple tasks at once... see pic examples

Details:
Whirlwind Mabel open for business in Mercer County starting August 4, 2014. Taking reservations now!

What we can do to save YOU time:
Grocery Shopping
Gift Shopping, wrapping and shipping
General Errands
Travel Arrangements and Event Planning
Project Management and Organization

What YOU can do with the time YOU save:
Spend time with your kids, family and friends
Relax and enjoy life!

Grand Opening special - Buy 2 hours, get 1 free! *****I don't know if I will use this, what do you think?******

```html
<!DOCTYPE html>
<html lang="en">
<head>
<meta charset="utf-8">
<title>Whirlwind Mabel – Grand Opening Postcard</title>
<link rel="stylesheet" href="https://fonts.googleapis.com/css2?family=Alegreya+Sans+SC:wght@800&family=Ubuntu:wght@500;700&family=Euphoria+Script&display=swap">
<style>
  :root {
    --navy: #1f3566;
    --tan: #b99c7b;
    --pink: #e2566f;
    --teal: #6aa58b;
    --white: #ffffff;
    --paper: #f2ede6;
    --coral: #e98a7a;
    --cream: #efe7da;
  }
  * { box-sizing: border-box; margin: 0; padding: 0; }
  html, body {
    width: 1200px; height: 800px; overflow: hidden;
    background: var(--paper);
  }
  .postcard {
    position: relative;
    width: 1200px; height: 800px;
    background: var(--tan);
    overflow: hidden;
    font-family: "Ubuntu", Arial, sans-serif;
    color: var(--white);
  }
  .top-band {
    position: absolute; left: 0; top: 0;
    width: 100%; height: 152px;
    background: var(--navy);
    border-bottom: 5px solid var(--white);
  }
  .bottom-band {
    position: absolute; left: 0; bottom: 0;
    width: 100%; height: 26px;
    background: var(--navy);
    border-top: 5px solid var(--white);
  }
  .slogan {
    position: absolute; left: 38px; top: 68px;
    font-family: "Euphoria Script", cursive;
    font-size: 40px;
    color: var(--pink);
    letter-spacing: 0.5px;
  }
  .brand-name {
    position: absolute; right: 30px; top: 52px;
    font-family: "Ubuntu", Arial, sans-serif;
    font-weight: 700;
    font-size: 44px;
    letter-spacing: 1px;
    text-transform: uppercase;
    color: var(--teal);
  }
  .offer {
    position: absolute; left: 44px; top: 192px;
    font-family: "Alegreya Sans SC", Georgia, sans-serif;
    font-weight: 800;
    font-size: 40px;
    line-height: 45px;
    letter-spacing: 0.5px;
  }
  .announcement {
    position: absolute; left: 44px; top: 326px;
    font-size: 33px;
    line-height: 42px;
    font-weight: 500;
  }
  .reservations {
    position: absolute; left: 44px; top: 546px;
    font-size: 33px;
    line-height: 42px;
    font-weight: 500;
  }
  .contact {
    position: absolute; left: 44px; top: 680px;
    list-style: none;
  }
  .contact-item {
    display: flex; align-items: center; gap: 12px;
  }
  .contact-phone {
    font-size: 34px; font-weight: 700; letter-spacing: 0.5px;
  }
  .contact-email {
    margin-top: 12px;
    font-family: "Alegreya Sans SC", Georgia, sans-serif;
    font-weight: 800;
    font-size: 24px;
    letter-spacing: 0.5px;
  }
  .contact-item svg { flex: none; }
  .illustration {
    position: absolute; left: 496px; top: 190px;
    width: 672px; height: 580px;
  }
</style>
</head>
<body>
  <main class="postcard">
    <header class="top-band">
      <p class="slogan">" We whirl around so you don't have to! "</p>
      <p class="brand-name">Whirlwind Mabel</p>
    </header>

    <h1 class="offer">Grand Opening Special:<br>Buy 2 Hours, Get 1 Free!</h1>

    <p class="announcement">Whirlwind Mabel Open For<br>Business In<br>Mercer County Starting<br>August 4, 2014.</p>

    <p class="reservations">Taking<br>Reservations Now!</p>

    <ul class="contact">
      <li class="contact-item contact-phone">
        <svg width="26" height="22" viewBox="0 0 26 22" aria-hidden="true">
          <path d="M2 7 Q13 -1 24 7 L21 10 L17 8 L17 5 Q13 4 9 5 L9 8 L5 10 Z" fill="#fff"/>
          <rect x="5" y="11" width="16" height="10" rx="2" fill="#fff"/>
        </svg>
        724-555-0186
      </li>
      <li class="contact-item contact-email">
        <svg width="26" height="18" viewBox="0 0 26 18" aria-hidden="true">
          <rect x="1" y="1" width="24" height="16" rx="1" fill="#fff"/>
          <path d="M1 1 L13 10 L25 1" fill="none" stroke="#b99c7b" stroke-width="2"/>
        </svg>
        mabel@whirlwindmabel.biz
      </li>
    </ul>

    <svg class="illustration" viewBox="0 0 672 580" role="img"
         aria-label="Retro cartoon of a multi-armed housewife in a red apron juggling a frying pan with eggs and bacon, a baby, a laptop, a milk bottle, a vacuum cleaner, a grocery bag with bread and a small dog on a leash">
      <defs>
        <linearGradient id="illustration-tone" x1="0" y1="0" x2="1" y2="1">
          <stop offset="0" stop-color="#f3ece2"/>
          <stop offset="0.55" stop-color="#e98a7a"/>
          <stop offset="1" stop-color="#c8a06a"/>
        </linearGradient>
      </defs>
      <path d="M40 40 L620 20 L660 560 L20 570 Z" fill="url(#illustration-tone)" stroke="#fff" stroke-width="8" stroke-linejoin="round"/>
    </svg>

    <footer class="bottom-band"></footer>
  </main>
</body>
</html>
```